Beacon Advisory Website

I currently have a website www.beaconadvisoryinc.com. We are a IT Consulting Company. Our website will pretty much tell out our services. I am looking to enhance my website and make it look more professional. Looking for very classy and Contemporary look and design for my website.

It Company

```html
<!DOCTYPE html>
<html lang="en">
<head>
<meta charset="utf-8">
<title>Beacon Advisory</title>
<link href="https://fonts.googleapis.com/css2?family=Questrial&family=Lato:wght@400;700&display=swap" rel="stylesheet">
<style>
:root{
  --blue:#1565b0;
  --sky:#1aa3e0;
  --text:#8a8a8a;
  --dark:#333;
  --line:#d8d8d8;
  --panel:#f0f0f0;
  --footer:#2b2b2b;
}
*{margin:0;padding:0;box-sizing:border-box}
html,body{width:778px;height:1200px;overflow:hidden;background:#fff}
body{position:relative;font-family:"Lato",sans-serif;color:var(--text)}
.hero{position:absolute;left:0;top:0;width:778px;height:425px;
  background:radial-gradient(ellipse at 55% 45%,#4d5a5e 0%,#323c40 45%,#1c2225 100%)}
.brand{position:absolute;left:0;right:0;top:180px;display:flex;justify-content:center;align-items:center;gap:14px}
.brand-dot{width:40px;height:40px;border-radius:50%;background:var(--sky)}
.brand-name{font-family:"Lato",sans-serif;font-weight:700;font-size:36px;color:#fff;letter-spacing:2px}
.nav{position:absolute;left:0;top:425px;width:778px;height:41px;border-bottom:1px solid var(--line);
  font-family:"Questrial",sans-serif;font-size:10.5px;color:#555}
.nav a{position:absolute;top:0;height:41px;line-height:42px;text-decoration:none;color:inherit;transform:translateX(-50%)}
.nav a.active{color:var(--blue);border-bottom:1px solid var(--blue);padding:0 8px}
.welcome{position:absolute;left:0;top:508px;width:778px;text-align:center}
.welcome h1{font-family:"Questrial",sans-serif;font-weight:400;font-size:21px;color:var(--blue);letter-spacing:.3px}
.welcome p{width:540px;margin:22px auto 0;font-size:10.4px;line-height:20.2px;color:var(--text)}
.more{position:absolute;left:305px;top:683px;width:168px;height:40px;border:1px solid var(--sky);border-radius:20px;
  font-family:"Questrial",sans-serif;font-size:11px;color:var(--blue);text-align:center;line-height:39px}
.feature{position:absolute;top:762px;width:200px}
.feature svg{position:absolute;left:-38px;top:0}
.feature h3{font-family:"Lato",sans-serif;font-weight:400;font-size:13.5px;color:var(--dark)}
.feature p{margin-top:8px;font-size:8.8px;line-height:13.6px;color:var(--text)}
.map{position:absolute;left:0;top:872px;width:389px;height:270px;background:linear-gradient(135deg,#ece8df,#e3e0d6 60%,#ddd9cc)}
.offices{position:absolute;left:389px;top:872px;width:389px;height:270px;background:var(--panel)}
.office{position:absolute;left:0}
.office svg{position:absolute;left:42px;top:0}
.office h4{position:absolute;top:0;font-weight:400;font-size:13px;color:var(--sky);white-space:nowrap}
.office address{position:absolute;top:22px;font-style:normal;font-size:9px;line-height:13.6px;color:#444;white-space:nowrap}
.footer{position:absolute;left:0;top:1142px;width:778px;height:58px;background:var(--footer);
  text-align:center;line-height:58px;font-size:9px;color:#eee}
.footer span{color:var(--sky)}
</style>
</head>
<body>
<header class="hero" role="img" aria-label="Photo of business consultants meeting around a table">
  <div class="brand"><span class="brand-dot"></span><span class="brand-name">BEACON ADVISORY</span></div>
</header>

<nav class="nav">
  <a class="active" href="#" style="left:135px">Home</a>
  <a href="#" style="left:213px">About Us</a>
  <a href="#" style="left:295px">Services</a>
  <a href="#" style="left:376px">Solutions</a>
  <a href="#" style="left:467px">Resources</a>
  <a href="#" style="left:551px">Career</a>
  <a href="#" style="left:630px">Contact Us</a>
</nav>

<section class="welcome">
  <h1>WELCOME TO BEACON ADVISORY</h1>
  <p>Today’s IT market is a dynamic, fast-paced industry, with ever-increasing demands. Meeting these demands for over 25 years, Beacon Advisory maintains a global presence, aggressively recruiting expertly qualified IT and Management Professionals from around the world and cultivating key partnerships with corporations to understand their business models end-to-end, with a goal of delivering exceptional client service and ensuring a consistent delivery of the talent needed to drive results.</p>
</section>
<div class="more">KNOW MORE</div>

<div class="feature" style="left:85px">
  <svg width="28" height="38" viewBox="0 0 28 38"><circle cx="14" cy="12" r="10" fill="none" stroke="#555" stroke-width="1.5"/><path d="M8 11a6 5 0 0 1 12 0z" fill="#8cbf3f"/><path d="M8 11h12l-3 4H11z" fill="#f0a030"/><path d="M10 22h8M10 26h8M11 30h6M12 34h4" stroke="#555" stroke-width="1.5"/></svg>
  <h3>Consulting</h3>
  <p>Beacon Advisory has certified professional consultants to work with you to help increase the business.</p>
</div>
<div class="feature" style="left:332px">
  <svg width="36" height="36" viewBox="0 0 36 36"><path d="M4 18a14 14 0 0 1 28 0" fill="none" stroke="#d9302c" stroke-width="3"/><path d="M32 18a14 14 0 0 1-28 0" fill="none" stroke="#1e7fc0" stroke-width="3"/><circle cx="18" cy="14" r="5" fill="#333"/><path d="M9 28a9 7 0 0 1 18 0z" fill="#333"/></svg>
  <h3>Staff Augmentation</h3>
  <p>For years Beacon Advisory as been offering our customers the ability to augment their existing staff</p>
</div>
<div class="feature" style="left:579px">
  <svg width="34" height="36" viewBox="0 0 34 36"><circle cx="17" cy="19" r="13" fill="#2f8fd0"/><path d="M8 14c5 2 6 8 3 12M20 8c2 5 8 6 10 10" fill="none" stroke="#6bb640" stroke-width="4"/><circle cx="5" cy="6" r="3" fill="#555"/><circle cx="29" cy="6" r="3" fill="#555"/></svg>
  <h3>Offshore</h3>
  <p>Our Offshore development model has a unique distinction of providing efficient software solutions</p>
</div>

<div class="map" role="img" aria-label="Street map showing the technical center location"></div>

<section class="offices">
  <div class="office" style="top:22px">
    <svg width="26" height="22" viewBox="0 0 26 22"><path d="M2 21h22M5 21V8l8-5v18M13 6h8v15" fill="none" stroke="var(--sky)" stroke-width="2"/><path d="M8 11v2M8 15v2M17 10v2M17 14v2" stroke="var(--sky)" stroke-width="1.5"/></svg>
    <h4 style="left:79px">Head Office</h4>
    <address style="left:79px">1200 Harbor Ave<br>Suite 210<br>Westfield, NJ 07090</address>
  </div>
  <div class="office" style="top:99px">
    <svg width="24" height="22" viewBox="0 0 24 22"><path d="M3 11a9 8 0 0 1 18 0" fill="none" stroke="var(--sky)" stroke-width="3"/><rect x="2" y="10" width="5" height="7" rx="2" fill="var(--sky)"/><rect x="17" y="10" width="5" height="7" rx="2" fill="var(--sky)"/><path d="M19 17c0 3-3 4-6 4" fill="none" stroke="var(--sky)" stroke-width="1.5"/></svg>
    <h4 style="left:73px">Technical Center</h4>
    <address style="left:73px">42100 W 12 Mile Road<br>Suite 300<br>Novi Park MI 48375</address>
  </div>
  <div class="office" style="top:182px">
    <svg width="22" height="24" viewBox="0 0 22 24"><rect x="3" y="3" width="14" height="20" fill="none" stroke="var(--sky)" stroke-width="2"/><path d="M7 7h2M11 7h2M7 11h2M11 11h2M7 15h2M11 15h2M1 23h20" stroke="var(--sky)" stroke-width="1.5"/></svg>
    <h4 style="left:79px">West Coast Office</h4>
    <address style="left:79px">1850 Terrace Place<br>Suite 400<br>San Mateo, CA 94401</address>
  </div>
</section>

<footer class="footer">© <span>BEACON ADVISORY</span> - 2016, All Right Reserved.</footer>
</body>
</html>
```